Corportate Power Point Template

We need a corporate PPT Design for our startup Big Data company.

Basically, our company will ingest, analyze and generate dynamic Dashboards with data consumed from different sources like Social Networks, Enterprise Legacy Systems such as e-Commerce, ERP, CRM and others.

Company is headquartered in Brazil, but will have a global presence.

Industry/Entity Type

It Company

```html
<!DOCTYPE html>
<html lang="en">
<head>
<meta charset="utf-8">
<title>Project Title Slide</title>
<link href="https://fonts.googleapis.com/css2?family=Rajdhani:wght@500;600&display=swap" rel="stylesheet">
<style>
  :root {
    --slide-bg: #efeeef;
    --footer-bg: #ffffff;
    --accent: #f15a1f;
    --title-grey: #6f6f6f;
    --text-dark: #2b2b2b;
    --marker: #0a0a0a;
    --frame-line: #d9d9d9;
    --placeholder-text: #c4c4c4;
    --divider: #bdbdbd;
  }
  * { margin: 0; padding: 0; box-sizing: border-box; }
  html, body {
    width: 1200px;
    height: 900px;
    overflow: hidden;
    background: var(--slide-bg);
  }
  .slide {
    position: relative;
    width: 1200px;
    height: 900px;
    background: var(--slide-bg);
    font-family: "Rajdhani", "Arial Narrow", sans-serif;
    color: var(--text-dark);
  }
  .title-marker {
    position: absolute;
    left: 0;
    top: 27px;
    width: 15px;
    height: 70px;
    background: var(--marker);
  }
  .slide-title {
    position: absolute;
    left: 25px;
    top: 28px;
    font-size: 57px;
    font-weight: 500;
    line-height: 70px;
    letter-spacing: 0;
    color: var(--title-grey);
    white-space: nowrap;
  }
  .slide-title .highlight { color: var(--accent); }
  .content {
    position: absolute;
    left: 31px;
    top: 152px;
    width: 660px;
  }
  .section-heading {
    font-size: 36px;
    font-weight: 600;
    line-height: 52px;
    color: var(--accent);
    margin-bottom: 12px;
    letter-spacing: 0.9px;
    white-space: nowrap;
  }
  .body-copy {
    font-size: 21px;
    font-weight: 500;
    line-height: 36px;
    margin-bottom: 36px;
    letter-spacing: 1.2px;
    white-space: nowrap;
  }
  .image-slot {
    position: absolute;
    left: 712px;
    width: 438px;
    height: 211px;
    background: #ffffff;
    border: 1px solid var(--frame-line);
    border-radius: 4px;
    display: flex;
    align-items: center;
    justify-content: center;
    font-size: 20px;
    font-weight: 500;
    color: var(--placeholder-text);
  }
  .image-slot.top { top: 207px; }
  .image-slot.bottom { top: 457px; }
  .footer {
    position: absolute;
    left: 0;
    top: 807px;
    width: 1200px;
    height: 93px;
    background: var(--footer-bg);
    border-top: 2px solid var(--divider);
    display: flex;
    align-items: center;
    justify-content: space-between;
    padding: 0 12px 0 18px;
  }
  .brand {
    font-size: 36px;
    font-weight: 600;
    color: var(--text-dark);
  }
  .copyright {
    font-size: 21px;
    font-weight: 500;
    color: var(--text-dark);
    letter-spacing: 0.6px;
  }
</style>
</head>
<body>
<div class="slide">
  <div class="title-marker"></div>
  <h1 class="slide-title"><span class="highlight">PROJECT</span> TITLE HERE</h1>

  <div class="content">
    <h2 class="section-heading">Lorem ipsum dolor sit ipsum</h2>
    <p class="body-copy">Lorem ipsum dolor sit ipsum Lorem ipsum dolor sit ipsum Lorem<br>ipsum dolor sit ipsum Lorem ipsum dolor sit ipsum lorem ipsum<br>dolor sit ipsum Lorem ipsum dolor sit ipsum Lorem ipsum dolor<br>sit ipsum</p>
    <p class="body-copy">Lorem ipsum dolor sit ipsum Lorem ipsum dolor sit ipsum Lorem<br>ipsum dolor sit ipsum Lorem ipsum dolor sit ipsum lorem ipsum<br>dolor sit ipsum Lorem ipsum dolor sit ipsum Lorem ipsum dolor<br>sit ipsum Lorem ipsum dolor sit ipsum</p>
    <p class="body-copy">Lorem ipsum dolor sit ipsum Lorem ipsum dolor sit ipsum Lorem<br>ipsum dolor sit ipsum Lorem ipsum dolor sit ipsum lorem ipsum<br>dolor sit ipsum Lorem ipsum dolor sit ipsum Lorem ipsum dolor<br>sit ipsum</p>
  </div>

  <div class="image-slot top">IMG HERE</div>
  <div class="image-slot bottom">IMG HERE</div>

  <footer class="footer">
    <div class="brand">Corvanta Data</div>
    <div class="copyright">Copyright text here</div>
  </footer>
</div>
</body>
</html>
```